Irrigation Business needs their business cards modernised and revamped

I would like to keep my current logo, colours and revamp the format of the card.

I would like the card to be clean yet important.

Im not sure if you include texture but i would like the named logo to be indented into the card etc.

show me something alive and free something thats clinical to the point yet has a feel of achievement. i would like people to go nice card.

Target Market(s)

high end clients, corporate, sports field manger, the guys that make the decisions

Industry/Entity Type

Business

Contact Information for Business Card

nformation to be included

Dean Harlow (Director)
0487305526
dean@kolvat.biz
www.kestonfieldworks.com

instagram logo
google logo
facebook logo

Colors

Designer to choose colors to be used in the design.

Requirements
Nice to have
• indentations a really nice feel to the card good texture

```html
<!DOCTYPE html>
<html lang="en">
<head>
<meta charset="utf-8">
<title>Keston Fieldworks – Business Card</title>
<link href="https://fonts.googleapis.com/css2?family=Roboto:wght@400;500;700&display=swap" rel="stylesheet">
<style>
  :root {
    --backdrop: #e4e4e4;
    --card: #f6f7f8;
    --card-edge: #ffffff;
    --navy: #2e4a8c;
    --sky: #3a8fc6;
    --ink: #2b2b2b;
    --ghost: rgba(200, 212, 226, 0.35);
    --white: #ffffff;
  }
  * { box-sizing: border-box; margin: 0; padding: 0; }
  html, body {
    width: 1200px; height: 576px; overflow: hidden;
    background: var(--backdrop);
    font-family: "Roboto", Arial, sans-serif;
  }
  .canvas { position: relative; width: 1200px; height: 576px; }

  .card {
    position: absolute; top: 138px;
    width: 484px; height: 294px;
    border-radius: 12px; overflow: hidden;
    background: linear-gradient(135deg, var(--card-edge) 0%, var(--card) 60%, #eceef1 100%);
    box-shadow: 0 3px 8px rgba(0,0,0,0.18);
  }
  .card--front { left: 82px; }
  .card--back { left: 602px; width: 481px; }

  .ghost-ring {
    position: absolute; border-radius: 50%;
    border: 14px solid var(--ghost);
    background: rgba(210, 220, 232, 0.18);
  }
  .card--front .ghost-ring { left: 302px; top: 14px; width: 224px; height: 224px; }
  .card--back .ghost-ring { left: 340px; top: 6px; width: 230px; height: 230px; }

  .brand-mark {
    position: absolute; border-radius: 50%;
    background: var(--sky);
    border: 3px solid var(--navy);
  }
  .card--front .brand-mark { left: 196px; top: 56px; width: 92px; height: 92px; }
  .card--back .brand-mark { left: 76px; top: 68px; width: 88px; height: 88px; }

  .brand-name {
    position: absolute; left: 0; text-align: center;
    color: var(--navy); font-weight: 700; letter-spacing: -0.3px;
    white-space: nowrap;
  }
  .card--front .brand-name { top: 158px; width: 484px; font-size: 29px; }
  .card--back .brand-name { top: 162px; left: 20px; width: 200px; font-size: 18px; }

  .social-row {
    position: absolute; left: 80px; top: 264px; width: 324px; height: 18px;
  }

  .holder { position: absolute; left: 246px; top: 84px; }
  .holder__name { color: var(--navy); font-size: 20px; font-weight: 700; letter-spacing: 0.2px; }
  .holder__role { color: var(--ink); font-size: 12px; margin-top: 4px; }

  .contacts { position: absolute; left: 250px; top: 137px; list-style: none; }
  .contacts li {
    display: flex; align-items: center; gap: 9px;
    height: 17px; font-size: 12.5px; color: var(--ink);
  }
  .contacts svg { width: 10px; height: 10px; flex: none; }

  .footer-band { position: absolute; left: 0; top: 256px; width: 481px; height: 38px; }
  .follow {
    position: absolute; left: 246px; top: 268px;
    color: var(--white); font-size: 13px;
  }
  .follow-icons { position: absolute; left: 331px; top: 266px; width: 60px; height: 20px; }
</style>
</head>
<body>
<main class="canvas">

  <section class="card card--front" aria-label="Card front">
    <div class="ghost-ring"></div>
    <div class="brand-mark"></div>
    <div class="brand-name">KESTON FIELDWORKS</div>
    <svg class="social-row" viewBox="0 0 324 18" aria-label="Social links">
      <line x1="0" y1="9" x2="117" y2="9" stroke="var(--navy)" stroke-width="2"/>
      <line x1="206" y1="9" x2="324" y2="9" stroke="var(--navy)" stroke-width="2"/>
      <circle cx="142" cy="9" r="8" fill="var(--navy)"/>
      <circle cx="162" cy="9" r="8" fill="var(--navy)"/>
      <circle cx="182" cy="9" r="8" fill="var(--navy)"/>
    </svg>
  </section>

  <section class="card card--back" aria-label="Card back">
    <div class="ghost-ring"></div>
    <div class="brand-mark"></div>
    <div class="brand-name">KESTON FIELDWORKS</div>

    <div class="holder">
      <div class="holder__name">DEAN HARLOW</div>
      <div class="holder__role">Director</div>
    </div>

    <ul class="contacts">
      <li>
        <svg viewBox="0 0 10 10"><path d="M1 3.5C1 2 2.5 1 5 1s4 1 4 2.5L7.5 4 7 3H3L2.5 4ZM2 5h6l1 4H1Z" fill="var(--navy)"/></svg>
        0487305526
      </li>
      <li>
        <svg viewBox="0 0 10 10"><rect x="0.5" y="2" width="9" height="6.5" fill="var(--navy)"/><path d="M0.5 2 5 5.5 9.5 2" stroke="var(--white)" stroke-width="0.9" fill="none"/></svg>
        dean@kolvat.biz
      </li>
      <li>
        <svg viewBox="0 0 10 10"><circle cx="5" cy="5" r="4.3" fill="none" stroke="var(--navy)" stroke-width="1"/><ellipse cx="5" cy="5" rx="1.8" ry="4.3" fill="none" stroke="var(--navy)" stroke-width="0.8"/><line x1="0.7" y1="5" x2="9.3" y2="5" stroke="var(--navy)" stroke-width="0.8"/></svg>
        www.kestonfieldworks.com
      </li>
    </ul>

    <svg class="footer-band" viewBox="0 0 481 38" preserveAspectRatio="none">
      <rect x="0" y="18" width="220" height="20" fill="var(--sky)"/>
      <polygon points="214,0 481,0 481,38 202,38" fill="var(--navy)"/>
    </svg>
    <div class="follow">Follow us on:</div>
    <svg class="follow-icons" viewBox="0 0 60 20" aria-label="Social links">
      <circle cx="9" cy="10" r="8" fill="none" stroke="var(--white)" stroke-width="1.5"/>
      <circle cx="29" cy="10" r="8" fill="none" stroke="var(--white)" stroke-width="1.5"/>
      <circle cx="49" cy="10" r="8" fill="none" stroke="var(--white)" stroke-width="1.5"/>
    </svg>
  </section>

</main>
</body>
</html>
```